Harborline Renewal Business Card Design

Professional and clean design. The design colors should flow with the logo. Two-sided card with the website on the back which is:

www.HarborlineRenewal.example.

"Specializing in Water Damage Restoration"

On the front I need the name, email, phone, and logo.

Name: Darnell Quisby
Email: Darnell@HarborlineRenewal.example
Phone: 555-318-2046 for now

I only have the Preview and Thumbnail right now but should have the source files uploaded within a day or two.

Target Market(s)

Flood victims, home owners with water damage from busted pipes etc...

Industry/Entity Type

Business

Contact Information for Business Card

Name: Darnell Quisby

Font styles to use
Serif
Sans Serif

Requirements
Must have
• Business Card Details Info

```html
<!DOCTYPE html>
<html lang="en">
<head>
<meta charset="utf-8">
<title>Harborline Renewal Business Card</title>
<link href="https://fonts.googleapis.com/css2?family=Cormorant+Garamond:wght@500;600;700&display=swap" rel="stylesheet">
<style>
  :root {
    --page: #ecebe8;
    --card-white: #f7f7f7;
    --charcoal: #3a3a3c;
    --charcoal-deep: #2e2e30;
    --sky: #4fc3ea;
    --sky-soft: #7fd6f2;
    --ocean: #1f9fd0;
    --ink-light: #f1f1f1;
    --ink-muted: #d6d6d6;
  }
  * { box-sizing: border-box; margin: 0; padding: 0; }
  html, body { width: 1200px; height: 1023px; overflow: hidden; }
  body {
    background: var(--page);
    font-family: "Cormorant Garamond", Georgia, serif;
    position: relative;
  }
  .card {
    position: absolute;
    top: 179px;
    width: 380px;
    height: 665px;
    border-radius: 4px;
    overflow: hidden;
    box-shadow: 0 6px 18px rgba(0,0,0,0.18);
  }
  .card-front { left: 180px; background: var(--card-white); }
  .card-back {
    left: 640px;
    background: linear-gradient(160deg, var(--sky) 0%, var(--ocean) 100%);
  }
  .front-shapes { position: absolute; inset: 0; }
  .brand {
    position: absolute;
    top: 92px;
    left: 0; right: 0;
    display: flex;
    align-items: center;
    justify-content: center;
    gap: 14px;
  }
  .brand-dot {
    width: 46px; height: 46px;
    border-radius: 50%;
    background: var(--sky);
    flex: none;
  }
  .brand-name {
    color: var(--sky);
    font-weight: 700;
    font-size: 30px;
    line-height: 1.0;
    letter-spacing: 2px;
    text-transform: uppercase;
  }
  .person {
    position: absolute;
    top: 378px;
    right: 34px;
    text-align: right;
  }
  .person-name {
    color: var(--sky);
    font-weight: 700;
    font-size: 27px;
    line-height: 1.1;
  }
  .person-role {
    color: var(--ink-muted);
    font-weight: 500;
    font-size: 17px;
    margin-top: 2px;
  }
  .contact-list {
    position: absolute;
    top: 468px;
    left: 30px;
    list-style: none;
  }
  .contact-item {
    display: flex;
    align-items: center;
    gap: 12px;
    height: 32px;
    color: var(--ink-light);
    font-size: 15.5px;
    font-weight: 500;
  }
  .contact-icon {
    width: 22px; height: 22px;
    background: var(--sky);
    border-radius: 2px;
    flex: none;
    display: flex;
    align-items: center;
    justify-content: center;
  }
  .back-content {
    position: absolute;
    inset: 0;
    display: flex;
    flex-direction: column;
    align-items: center;
    justify-content: center;
    text-align: center;
    color: #ffffff;
  }
  .back-name {
    font-weight: 700;
    font-size: 36px;
    letter-spacing: 3px;
    text-transform: uppercase;
    line-height: 1.05;
  }
  .back-rule {
    width: 220px; height: 1px;
    background: rgba(255,255,255,0.7);
    margin: 16px 0 14px;
  }
  .back-site {
    font-weight: 500;
    font-size: 18px;
    letter-spacing: 0.5px;
  }
</style>
</head>
<body>
  <section class="card card-front" aria-label="Front of card">
    <svg class="front-shapes" width="380" height="665" viewBox="0 0 380 665" aria-hidden="true">
      <path d="M0,232 Q170,350 380,318 L380,344 Q170,372 0,258 Z" fill="var(--sky-soft)"/>
      <path d="M0,246 Q170,360 380,330 L380,340 Q170,368 0,256 Z" fill="var(--sky)"/>
      <path d="M0,258 Q170,372 380,344 L380,665 L0,665 Z" fill="var(--charcoal)"/>
    </svg>

    <div class="brand">
      <span class="brand-dot"></span>
      <span class="brand-name">Harborline<br>Renewal</span>
    </div>

    <div class="person">
      <p class="person-name">Darnell Quisby</p>
      <p class="person-role">Owner / Founder</p>
    </div>

    <ul class="contact-list">
      <li class="contact-item">
        <span class="contact-icon">
          <svg width="14" height="14" viewBox="0 0 24 24" aria-hidden="true"><path fill="#fff" d="M6.6 10.8a15.1 15.1 0 0 0 6.6 6.6l2.2-2.2a1 1 0 0 1 1-.25 11.4 11.4 0 0 0 3.6.57 1 1 0 0 1 1 1V20a1 1 0 0 1-1 1A17 17 0 0 1 3 4a1 1 0 0 1 1-1h3.5a1 1 0 0 1 1 1c0 1.25.2 2.45.57 3.57a1 1 0 0 1-.25 1z"/></svg>
        </span>
        555-318-2046
      </li>
      <li class="contact-item">
        <span class="contact-icon">
          <svg width="14" height="14" viewBox="0 0 24 24" aria-hidden="true"><rect x="2" y="5" width="20" height="14" fill="none" stroke="#fff" stroke-width="2"/><path d="M2 5l10 8 10-8" fill="none" stroke="#fff" stroke-width="2"/></svg>
        </span>
        Darnell@HarborlineRenewal.example
      </li>
      <li class="contact-item">
        <span class="contact-icon"></span>
        gallery.HarborlineRenewal.example
      </li>
      <li class="contact-item">
        <span class="contact-icon"></span>
        news.HarborlineRenewal.example
      </li>
    </ul>
  </section>

  <section class="card card-back" aria-label="Back of card">
    <div class="back-content">
      <p class="back-name">Harborline<br>Renewal</p>
      <span class="back-rule"></span>
      <p class="back-site">www.HarborlineRenewal.example</p>
    </div>
  </section>
</body>
</html>
```